Manufacturer of prepared Persian ready meals needs a product concept design

I need a product concept design for a new company based in the UK called 'Valdren Kitchen Ltd'.
The winner will potentially be selected to produce prototype designs for our other products.
For this project, the product will be called "Ghormeh Sabzi". This needs to be on the design to let consumers know what it is.
Whilst still in the concept stage, the aim of the company is to produce refrigerated microwaveable / oven Persian ready meal for retail supermarket consumers, and may also have an online platform for direct to consumer sales.
I have provided quite a few competitor examples of products.
I would like the product in a black or clear round bowl. It will be split into two sections (Half stew / Half rice) by the sleeve, which you are designing. I would like the food to be visible on either side of the label, so the consumer knows what they are eating.
The logo is provided within the file attachments and needs to be on prominent display on the pouch.
The mission for Valdren Kitchen Ltd brand is:
"Bringing 2,500 years of scented history to your table".
This needs to be present on the sleeve.
The product needs to represent the ethnicity of the brand throughout the design, and the same font to be used throughout.
Persian architecture was filled with a wide range of vibrant colours and has been engineered to stand the test of time, so I would like that to be incorporated into the product design (see attached examples of Persian geometry).
Alternatively Persian carpets are world renowned for their quality, so examples of this could be displayed on the packaging.
These will have to be artistically interpreted to avoid potential copyright; I am looking for individual artistic design.
It needs to represent a super quality, royalty & decadence throughout, and stand out on the shelves to the consumer above all the other competitor products.
To comply with food standards, the sleeve must have a nutritional label on display. I have attached a generic example for you to use. You may create your own representation of it.
Ghormeh Sabzi is a natural source of fibre, high in protein, gluten and dairy free, so I would like this displayed on the sleeve, as well as the the words:
- Traditionally rich in aromatic herbs, tender slow cooked lamb, red kidney beans & dried limes
- One of the oldest dishes in Persian history
You can find pictures of the food provided in the files. Note, these are not my pictures, but give you an idea of what will be provided inside.
Some designers have uploaded the same design up to 5 times, others twice. Only 18 have been uploaded, but it says 20, so I think 2 have been removed?

```html
<!DOCTYPE html>
<html lang="en">
<head>
<meta charset="utf-8">
<title>Ghormeh Sabzi – Valdren Kitchen sleeve</title>
<link href="https://fonts.googleapis.com/css2?family=Archivo+Black&family=Barlow+Condensed:wght@400;500;600&family=Josefin+Sans:wght@400;600&display=swap" rel="stylesheet">
<style>
  :root {
    --bg: #bdbdbd;
    --sleeve-green: #0d4630;
    --sleeve-deep: #08382a;
    --yellow: #ece356;
    --teal: #1f8a6e;
    --teal-line: #2fae8a;
    --white: #f4f4ee;
    --plate: #e4e1d6;
    --stew-dark: #2f3a12;
    --stew-mid: #4f5a1c;
    --energy: #2aa8d8;
    --saturates: #8cbf3a;
    --salt: #eeb021;
    --sugar: #e0253c;
    --fat: #efb024;
  }
  * { box-sizing: border-box; margin: 0; padding: 0; }
  html, body { width: 1200px; height: 1200px; overflow: hidden; }
  body { background: var(--bg); position: relative; font-family: "Barlow Condensed", sans-serif; }

  .sleeve {
    position: absolute; left: 360px; top: 40px; width: 480px; height: 1120px;
    background: linear-gradient(180deg, var(--sleeve-green), var(--sleeve-deep));
    overflow: hidden; color: var(--white); text-align: center;
  }
  .brand { position: absolute; top: 46px; left: 0; right: 0; display: flex; flex-direction: column; align-items: center; }
  .brand-mark { width: 46px; height: 46px; background: var(--yellow); margin-bottom: 22px; }
  .brand-name { font-family: "Josefin Sans", sans-serif; font-weight: 600; font-size: 34px; letter-spacing: 9px; color: var(--white); line-height: 1; }
  .brand-sub { font-family: "Josefin Sans", sans-serif; font-weight: 400; font-size: 15px; letter-spacing: 6px; color: var(--white); margin-top: 4px; }

  .title { position: absolute; top: 222px; left: 0; right: 0; font-family: "Archivo Black", sans-serif; color: var(--yellow); font-size: 70px; line-height: 0.92; }
  .title-ring { position: absolute; top: 278px; left: 26px; width: 340px; height: 110px; }
  .tagline { position: absolute; top: 404px; left: 0; right: 0; font-size: 22px; font-weight: 400; }
  .tagline em { font-style: italic; font-weight: 600; color: var(--yellow); }

  .claims { position: absolute; top: 466px; left: 0; right: 0; display: flex; justify-content: center; gap: 8px; }
  .claim { background: var(--teal); border: 1.5px solid var(--teal-line); border-radius: 16px; padding: 4px 12px; font-size: 15px; font-weight: 500; white-space: nowrap; }

  .description { position: absolute; top: 522px; left: 50px; right: 50px; font-size: 17px; line-height: 1.25; }
  .wave { position: absolute; top: 594px; left: 60px; width: 360px; height: 24px; }
  .heritage { position: absolute; top: 636px; left: 0; right: 0; font-family: "Archivo Black", sans-serif; font-size: 22px; line-height: 1.1; }
  .heritage span { display: block; color: var(--yellow); }

  .dish { position: absolute; top: 730px; left: -80px; width: 640px; height: 640px; border-radius: 50%; background: var(--yellow); }
  .dish-plate { position: absolute; inset: 14px; border-radius: 50%; background: var(--plate); }
  .dish-food { position: absolute; inset: 58px; border-radius: 50%;
    background: radial-gradient(circle at 50% 35%, var(--stew-mid), var(--stew-dark) 70%); }

  .nutrition { position: absolute; top: 1000px; left: 0; right: 0; display: flex; justify-content: center; gap: 10px; }
  .nutrient { width: 56px; height: 92px; border-radius: 6px 6px 28px 28px; color: var(--white); font-size: 12px; line-height: 1.1; padding-top: 4px; display: flex; flex-direction: column; align-items: center; border: 2px solid var(--white); }
  .nutrient-label { font-size: 8px; font-weight: 600; text-transform: uppercase; margin-bottom: 6px; }
  .nutrient-ri { margin-top: auto; margin-bottom: 5px; background: var(--white); color: #444; border-radius: 50%; width: 40px; height: 22px; line-height: 22px; font-size: 12px; }
  .energy { background: var(--energy); }
  .saturates { background: var(--saturates); }
  .salt { background: var(--salt); }
  .sugar { background: var(--sugar); }
  .fat { background: var(--fat); }
</style>
</head>
<body>
  <section class="sleeve">
    <header class="brand">
      <div class="brand-mark"></div>
      <div class="brand-name">VALDREN</div>
      <div class="brand-sub">KITCHEN</div>
    </header>

    <svg class="title-ring" viewBox="0 0 340 110" aria-hidden="true">
      <ellipse cx="170" cy="55" rx="166" ry="48" fill="none" stroke="var(--teal-line)" stroke-width="2.5"/>
    </svg>
    <h1 class="title">GHORMEH<br>SABZI</h1>

    <p class="tagline">Bringing <em>2,500 years</em> of scented history to your table</p>

    <ul class="claims">
      <li class="claim" style="list-style:none">Natural Source Of Fibre</li>
      <li class="claim" style="list-style:none">Gluten And Dairy Free</li>
      <li class="claim" style="list-style:none">High In Protein</li>
    </ul>

    <p class="description">Traditionally rich in aromatic herbs, tender slow cooked lamb, red kidney beans &amp; dried limes</p>

    <svg class="wave" viewBox="0 0 360 24" aria-hidden="true">
      <path d="M0 12 Q22.5 0 45 12 T90 12 T135 12 T180 12 T225 12 T270 12 T315 12 T360 12" fill="none" stroke="var(--yellow)" stroke-width="2"/>
    </svg>

    <p class="heritage">ONE OF THE OLDEST DISHES IN<span>PERSIAN HISTORY</span></p>

    <div class="dish">
      <div class="dish-plate"></div>
      <div class="dish-food" role="img" aria-label="Photo of Ghormeh Sabzi herb stew with lamb and kidney beans in a white bowl"></div>
    </div>

    <div class="nutrition">
      <div class="nutrient energy"><span class="nutrient-label">Energy</span>1046 kJ<br>250 kcal<span class="nutrient-ri">13%</span></div>
      <div class="nutrient saturates"><span class="nutrient-label">Saturates</span>1.3 g<br>Low<span class="nutrient-ri">7%</span></div>
      <div class="nutrient salt"><span class="nutrient-label">Salt</span>0.9 g<br>Medium<span class="nutrient-ri">15%</span></div>
      <div class="nutrient sugar"><span class="nutrient-label">Sugar</span>34 g<br>High<span class="nutrient-ri">38%</span></div>
      <div class="nutrient fat"><span class="nutrient-label">Fat</span>3.0 g<br>Low<span class="nutrient-ri">4%</span></div>
    </div>
  </section>
</body>
</html>
```